Gift Cards in the Mail Envelope

Mailing out gift cards in the envelope. Need an eye popping envelope. Please look at the enclosed images. The envelope should look like that.

Low design quality

```html
<!DOCTYPE html>
<html lang="en">
<head>
<meta charset="UTF-8">
<title>Gift Voucher Envelope</title>
<link rel="stylesheet" href="https://fonts.googleapis.com/css2?family=Caveat+Brush&family=Montserrat:wght@400;500&display=swap">
<style>
  :root {
    --backdrop: #d9d9d9;
    --envelope-yellow: #fefe0d;
    --ink: #000000;
  }
  * { margin: 0; padding: 0; box-sizing: border-box; }
  html, body {
    width: 1200px;
    height: 1200px;
    overflow: hidden;
    background: var(--backdrop);
  }
  .canvas {
    position: relative;
    width: 1200px;
    height: 1200px;
    background: var(--backdrop);
  }
  .envelope-face {
    position: absolute;
    left: 277px;
    width: 647px;
    height: 431px;
    background: var(--envelope-yellow);
    color: var(--ink);
    text-align: center;
  }
  .envelope-front { top: 154px; }
  .envelope-back { top: 618px; height: 430px; width: 646px; }

  .voucher-title {
    position: absolute;
    left: 0; right: 0;
    top: 135px;
    font-family: "Caveat Brush", cursive;
    font-weight: 400;
    font-size: 104px;
    line-height: 1;
    letter-spacing: 1px;
    text-transform: uppercase;
    transform: scaleY(1.05);
  }
  .voucher-subtitle {
    position: absolute;
    left: 0; right: 0;
    top: 243px;
    font-family: "Montserrat", sans-serif;
    font-weight: 400;
    font-size: 27px;
    line-height: 1;
  }
  .voucher-amount {
    position: absolute;
    left: 0; right: 0;
    top: 120px;
    font-family: "Caveat Brush", cursive;
    font-size: 44px;
    line-height: 1;
  }
  .voucher-prompt {
    position: absolute;
    left: 0; right: 0;
    top: 162px;
    font-family: "Montserrat", sans-serif;
    font-weight: 500;
    font-size: 12px;
    line-height: 1;
  }
</style>
</head>
<body>
  <main class="canvas">
    <section class="envelope-face envelope-front">
      <h1 class="voucher-title">Gift Voucher</h1>
      <p class="voucher-subtitle">It’s inside the envelope</p>
    </section>
    <section class="envelope-face envelope-back">
      <p class="voucher-amount">$100</p>
      <p class="voucher-prompt">Open me!</p>
    </section>
  </main>
</body>
</html>
```